Casino with the 'highest winning percentage' needs a stationery design

This is for a casino in Colombo, Sri Lanka and we need a stationery design for business card, letter head and envelope.

Should be very professional, simple and elegant without fancy fonts

Reason: Not fully satisfied with the designs. Need more designs.

Business

• 1. card deck symbol 'CLUBS' in red, or black

2. name in BLOCK CAPITAL LETTERS

3. Preferred font colours are black, white or red

4. Prefer 'professional /elegant' fonts
• SHOULD NOT HAVE ANY OTHER SYMBOL EXCEPT 'CLUBS'

DO NOT PREFER ITALIC FONTS

```html
<!DOCTYPE html>
<html lang="en">
<head>
<meta charset="utf-8">
<title>Orchid Casino – Letterhead</title>
<link href="https://fonts.googleapis.com/css2?family=Didact+Gothic&display=swap" rel="stylesheet">
<style>
  :root {
    --backdrop: #c9c9c9;
    --paper: #f7f7f7;
    --ink: #4a4a4a;
    --ink-strong: #222222;
    --ink-soft: #7a7a7a;
    --emboss-core: #e9e9e9;
    --emboss-fade: rgba(247,247,247,0);
  }
  html, body {
    margin: 0;
    padding: 0;
    width: 1200px;
    height: 1000px;
    overflow: hidden;
    background: var(--backdrop);
    font-family: "Didact Gothic", "Century Gothic", sans-serif;
  }
  .letterhead {
    position: absolute;
    left: 267px;
    top: 30px;
    width: 666px;
    height: 940px;
    background: var(--paper);
    box-shadow: 0 2px 10px rgba(0,0,0,0.12);
    color: var(--ink);
  }
  .brand {
    position: absolute;
    left: 56px;
    top: 44px;
    display: flex;
    flex-direction: column;
    align-items: flex-start;
    gap: 6px;
  }
  .brand-dot {
    width: 22px;
    height: 22px;
    border: 1.5px solid var(--ink);
    border-radius: 50%;
    margin-left: 4px;
    margin-bottom: 2px;
  }
  .brand-name {
    font-size: 20px;
    letter-spacing: 2px;
    line-height: 1.1;
    color: var(--ink);
  }
  .brand-tagline {
    font-size: 8px;
    letter-spacing: 0.4px;
    color: var(--ink-soft);
    line-height: 1.3;
  }
  .watermark {
    position: absolute;
    left: 143px;
    top: 230px;
    width: 380px;
    height: 300px;
    border-radius: 48%;
    background:
      radial-gradient(ellipse at 30% 35%, var(--emboss-core) 0%, var(--emboss-fade) 42%),
      radial-gradient(ellipse at 72% 35%, var(--emboss-core) 0%, var(--emboss-fade) 42%),
      radial-gradient(ellipse at 30% 72%, var(--emboss-core) 0%, var(--emboss-fade) 42%),
      radial-gradient(ellipse at 72% 72%, var(--emboss-core) 0%, var(--emboss-fade) 42%),
      radial-gradient(ellipse at 50% 53%, #eeeeee 0%, var(--emboss-fade) 65%);
  }
  .sender {
    position: absolute;
    right: 56px;
    bottom: 80px;
    display: flex;
    flex-direction: column;
    align-items: flex-end;
    text-align: right;
    font-size: 12px;
    line-height: 1.35;
    color: var(--ink);
  }
  .sender-web strong {
    font-weight: 400;
    color: var(--ink-strong);
    letter-spacing: 0.3px;
  }
  .sender-mark {
    margin-top: 14px;
    display: flex;
    align-items: center;
    gap: 8px;
    font-size: 12px;
    letter-spacing: 1.5px;
    color: var(--ink);
  }
  .sender-mark-dot {
    width: 18px;
    height: 18px;
    border: 1.5px solid var(--ink);
    border-radius: 50%;
  }
</style>
</head>
<body>
  <main class="letterhead">
    <header class="brand">
      <div class="brand-dot"></div>
      <div class="brand-name">ORCHID<br>CASINO</div>
      <div class="brand-tagline">Highest winning percentage<br>in the world</div>
    </header>

    <div class="watermark" role="img" aria-label="Faint blind-embossed brand decoration"></div>

    <footer class="sender">
      <div>ORCHID LIMITED</div>
      <div>12, Harbour View Mawatha</div>
      <div>Colombo 01000, Sri Lanka</div>
      <div>Tel: + 94 11 2000150</div>
      <div>Fax: + 94 11 2000160</div>
      <div class="sender-web">www.<strong>orchidcolombo</strong>.com</div>
      <div class="sender-mark"><span class="sender-mark-dot"></span>ORCHID</div>
    </footer>
  </main>
</body>
</html>
```